Website for enterprise software start-up

We need a new Wordpress website. We are an early stage start-up focused on mobile video technology for cellular operators. The audience is strategy, marketing and customer acquisition execs from the operators.

The purpose of the site is to act as a sales brochure and capture leads. A demo app can be downloaded from the current site, want to put that behind a contact form.

Current website is at www.velmora.tv. Similar number of pages. Looking for a clean design template, with minimal customization. Blog will remain as is.

Want to be able to modify the copy via Wordpress. Reference designs I like: quandrix.com, briskfold7metrics.com

Target Market(s)

Mobile operators and MVNOs in the US and Asia Pacific regions

Industry/Entity Type

Business Software

Coding

Coded - Design and coding required

Number of Pages Required

4 page

Font styles to use
Sans Serif

Colors
f78f20

Requirements
Must have
• Form for downloading sample apps.
• Landing page with image, Product, Blog, About, Contact
• Team page

```html
<!DOCTYPE html>
<html lang="en">
<head>
<meta charset="utf-8">
<title>Velmora Media</title>
<link rel="stylesheet" href="https://fonts.googleapis.com/css2?family=Raleway:wght@300;400;600;700&family=Lato:wght@400;700&display=swap">
<style>
:root{
  --orange:#f78f20;
  --orange-dark:#e06f0c;
  --ink:#2b2b2b;
  --text:#444;
  --muted:#777;
  --grey-band:#f1f1f1;
  --partner-band:#ebebeb;
  --white:#fff;
  --footer:#262626;
}
*{box-sizing:border-box;margin:0;padding:0}
html,body{width:1200px;height:3015px;overflow:hidden}
body{position:relative;background:var(--white);font-family:'Lato',Arial,sans-serif;color:var(--text)}
.abs{position:absolute}
.heading{font-family:'Raleway',Arial,sans-serif;font-weight:400;font-size:24px;color:var(--ink);border:1px solid #e2e2e2;border-left:none;padding:6px 10px 6px 0}
.heading b{color:var(--orange);font-weight:700}
.btn{background:var(--orange-dark);color:#fff;font:700 12px 'Lato',Arial,sans-serif;display:flex;align-items:center;justify-content:center;gap:8px}
.body-copy{font-size:11px;line-height:23px;color:#333}

/* header */
.site-header{left:0;top:0;width:1200px;height:78px;background:#fff;border-bottom:3px solid var(--orange)}
.brand{left:132px;top:20px;display:flex;align-items:center;gap:8px}
.brand-mark{width:40px;height:40px;background:var(--orange)}
.brand-name{font:700 32px/1 'Raleway',Arial,sans-serif;color:var(--ink)}
.nav{left:510px;top:34px;display:flex;font:400 11px 'Raleway',Arial,sans-serif;color:#333}
.nav span{margin-right:36px}
.login{left:976px;top:24px;width:88px;height:34px;background:#2b2b2b;color:#fff;font:700 11px 'Lato',Arial,sans-serif;display:flex;align-items:center;justify-content:center}

/* hero */
.hero{left:0;top:78px;width:1200px;height:476px;background:linear-gradient(100deg,#6b4a35 0%,#8a6a4e 28%,#a99c84 55%,#8e8a78 80%,#6d6a5c 100%)}
.hero-title{left:0;top:254px;width:1200px;text-align:center;color:#fff;font:400 36px 'Raleway',Arial,sans-serif}
.hero-sub{left:0;top:312px;width:1200px;text-align:center;color:#fff;font:400 17px 'Raleway',Arial,sans-serif}
.hero-btn{left:528px;top:360px;width:142px;height:32px;font:400 14px 'Raleway',Arial,sans-serif}

/* side labels */
.side-label{left:1030px;display:flex;flex-direction:column;align-items:center}
.side-label .tick{width:14px;height:1px;background:#222}
.side-label .rule{width:1px;background:#222}
.side-label .word{writing-mode:vertical-rl;font:300 28px 'Raleway',Arial,sans-serif;letter-spacing:14px;color:#222;margin-top:8px}

/* about */
.about-photo{background:linear-gradient(160deg,#2f3a2a,#55644a 50%,#1f2620)}
.about-photo.two{background:linear-gradient(160deg,#e8e6e2,#9ab0c6 50%,#4c5f78)}

/* product */
.product-band{left:0;top:958px;width:1200px;height:552px;background:var(--grey-band)}
.phone{left:148px;top:1084px;width:152px;height:316px;border:2px solid #555;border-radius:22px;background:#fafafa}
.phone-screen{left:162px;top:1128px;width:124px;height:228px;background:linear-gradient(150deg,#6b4b8a,#8aa06a 45%,#c8c2b6 70%,#4d6b3a)}
.phone-button{left:210px;top:1364px;width:26px;height:26px;border:2px solid #555;border-radius:50%}
.phone-speaker{left:204px;top:1104px;width:40px;height:4px;border-radius:2px;background:#999}
.feature-title{left:344px;top:1094px;font:400 24px 'Raleway',Arial,sans-serif;color:var(--orange);border-left:4px solid var(--orange);padding-left:8px}
.feature-lead{left:344px;top:1132px;width:520px;font-size:13px;line-height:17px;color:#333}
.feature-list{left:344px;top:1180px;list-style:none}
.feature-list li{display:flex;align-items:center;gap:12px;font-size:11px;color:#333;height:43.5px}
.pager{font:400 11px 'Raleway',Arial,sans-serif;color:#666;display:flex;align-items:center;gap:10px;border-bottom:1px solid #ccc;padding-bottom:4px}

/* sample apps */
.apps-band{left:0;top:1510px;width:1200px;height:320px;background:linear-gradient(110deg,#3f4a3f 0%,#6b6f63 35%,#8f8a7c 55%,#3b4f8a 75%,#8b2a22 100%)}
.apps-box{left:466px;top:1572px;width:266px;height:64px;background:rgba(255,255,255,.22);border:1px solid rgba(255,255,255,.4);display:flex;align-items:center;justify-content:center;color:#fff;font:400 24px 'Raleway',Arial,sans-serif}
.apps-box b{font-weight:600;margin-left:7px}
.store{top:1688px;width:116px;height:40px;background:#111;border:1px solid #aaa;border-radius:6px}

/* blog */
.post{width:400px;height:210px;border:1px solid #e6e6e6;background:#fff}
.post-photo{width:170px;height:200px}
.post-meta{font-size:11px;color:#444;display:flex;gap:16px;border-bottom:1px solid #e6e6e6;padding-bottom:6px;width:186px}
.post-title{font:700 13px 'Lato',Arial,sans-serif;color:#222}
.post-text{font-size:11px;line-height:16px;color:#444;width:190px}
.read-more{font:700 11px 'Lato',Arial,sans-serif;color:#222;display:flex;align-items:center;gap:6px;border-bottom:1px solid #ccc;padding-bottom:3px}

/* partners */
.partner-band{left:0;top:2310px;width:1200px;height:156px;background:var(--partner-band)}
.partner{top:2356px;height:74px;background:#fff;display:flex;align-items:center;justify-content:center;gap:8px;font:700 20px 'Lato',Arial,sans-serif;color:#444}
.dot{width:12px;height:12px;border-radius:50%;background:#7a7a7a}

/* contact */
.contact-band{left:0;top:2466px;width:1200px;height:498px;background:linear-gradient(100deg,#b9a889 0%,#d8cbb0 25%,#e8dcc4 45%,#b6906c 70%,#6f7f93 100%)}
.contact-title{left:0;top:2532px;width:1200px;text-align:center;color:#fff;font:400 28px 'Raleway',Arial,sans-serif}
.contact-title b{font-weight:600;border:1px solid rgba(255,255,255,.6);padding:0 8px}
.contact-sub{left:270px;top:2590px;width:660px;text-align:center;color:#fff;font:700 10px/16px 'Lato',Arial,sans-serif}
.info-panel{left:198px;top:2662px;width:300px;height:270px;background:rgba(255,255,255,.85);padding:22px 26px}
.info-panel h3{font:700 12px 'Lato',Arial,sans-serif;color:var(--orange);margin-bottom:10px}
.info-panel p{font-size:11px;line-height:17px;color:#222}
.info-row{display:flex;gap:14px;margin-top:16px;font-size:11px;line-height:18px;color:#222}
.form-panel{left:538px;top:2662px;width:446px;height:270px;background:rgba(255,255,255,.75)}
.field{left:560px;width:400px;background:rgba(255,255,255,.6);border-bottom:1px solid #ddd;font-size:11px;color:#333;padding:8px 10px}
.submit{left:560px;top:2880px;width:114px;height:32px}

/* footer */
.site-footer{left:0;top:2964px;width:1200px;height:51px;background:var(--footer);color:#ddd;font-size:12px}
.social{width:26px;height:26px;border-radius:2px}
</style>
</head>
<body>

<header class="site-header abs">
  <div class="brand abs"><span class="brand-mark"></span><span class="brand-name">velmora</span></div>
  <nav class="nav abs"><span>HOME</span><span>PRODUCT</span><span>BLOG</span><span>TEAM</span><span>ABOUT</span><span>CONTACT</span></nav>
  <div class="login abs">LOGIN</div>
</header>

<section class="hero abs" role="img" aria-label="Photo of a young woman with headphones looking at her phone outdoors"></section>
<h1 class="hero-title abs">High Quality Mobile Engagement™</h1>
<p class="hero-sub abs">We engage mobile audiences with the right video content at the perfect moment.</p>
<div class="btn hero-btn abs">Sample Apps</div>

<!-- about -->
<h2 class="heading abs" style="left:132px;top:626px">We Are <b>Velmora Media</b></h2>
<div class="body-copy abs" style="left:134px;top:694px;width:500px">
  <p>Lorem ipsum dolor sit amet, consectetuer adipiscing elit, sed diam nonummy nibh euismod tincidunt ut laoreet dolore magna aliquam erat volutpat. Ut wisi enim ad minim veniam, quis nostrud exerci tation ullamcorper suscipit lobortisnequat.</p>
  <p style="margin-top:8px">Duis autem vel eum iriure dolor in hendrerit in vulputate velit esse molestie consequat, vel illum dolore eu feugiat nulla facilisis at vero eros et accumsan et iusto odio dignissim qui blandit praesent luptatum zzril delenit augue duis dolore te feugait nulla facilisi.</p>
</div>
<div class="btn abs" style="left:132px;top:880px;width:118px;height:32px">Read More</div>
<div class="about-photo abs" style="left:672px;top:704px;width:144px;height:164px" role="img" aria-label="Photo of hands holding smartphones on grass"></div>
<div class="about-photo two abs" style="left:830px;top:660px;width:146px;height:162px" role="img" aria-label="Photo of a hand holding a smartphone"></div>
<div class="side-label abs" style="top:556px"><span class="tick"></span><span class="rule" style="height:104px"></span><span class="word">about-</span></div>

<!-- product -->
<div class="product-band abs"></div>
<h2 class="heading abs" style="left:132px;top:996px">Our <b>Product</b></h2>
<div class="phone abs"></div>
<div class="phone-speaker abs"></div>
<div class="phone-screen abs" role="img" aria-label="App screen showing a video thumbnail"></div>
<div class="phone-button abs"></div>
<h3 class="feature-title abs">Push Video Notifications</h3>
<p class="feature-lead abs">Personalised flawless HD videos, revealed at the perfect &nbsp;moment, as rich media notifications.</p>
<ul class="feature-list abs">
  <li><svg width="12" height="10" viewBox="0 0 12 10"><path d="M0 5h10M6 1l4 4-4 4" stroke="#555" stroke-width="1.6" fill="none"/></svg>Reach your mobile audience with beautiful HD thumbnails and in-notification videos.</li>
  <li><svg width="12" height="10" viewBox="0 0 12 10"><path d="M0 5h10M6 1l4 4-4 4" stroke="#555" stroke-width="1.6" fill="none"/></svg>Instant video playback, zero buffering, guaranteed flawless playback - even when offline.</li>
  <li><svg width="12" height="10" viewBox="0 0 12 10"><path d="M0 5h10M6 1l4 4-4 4" stroke="#555" stroke-width="1.6" fill="none"/></svg>Content is personalised based on viewer interests and mobile viewing habits.</li>
  <li><svg width="12" height="10" viewBox="0 0 12 10"><path d="M0 5h10M6 1l4 4-4 4" stroke="#555" stroke-width="1.6" fill="none"/></svg>Monetize with beautiful HD preroll or interstitial ads.</li>
  <li><svg width="12" height="10" viewBox="0 0 12 10"><path d="M0 5h10M6 1l4 4-4 4" stroke="#555" stroke-width="1.6" fill="none"/></svg>Easily added to your existing apps within one hour.</li>
</ul>
<div class="pager abs" style="left:132px;top:1440px;width:82px">
  <svg width="18" height="18" viewBox="0 0 18 18"><circle cx="9" cy="9" r="8" stroke="#333" fill="none"/><path d="M13 9H5M8 6L5 9l3 3" stroke="#333" fill="none"/></svg>Previous</div>
<div class="btn abs" style="left:526px;top:1434px;width:144px;height:34px">View All Product</div>
<div class="pager abs" style="left:982px;top:1440px;width:84px;justify-content:space-between">Next
  <svg width="18" height="18" viewBox="0 0 18 18"><circle cx="9" cy="9" r="8" stroke="#333" fill="none"/><path d="M5 9h8M10 6l3 3-3 3" stroke="#333" fill="none"/></svg></div>
<div class="side-label abs" style="top:958px"><span class="rule" style="height:104px"></span><span class="word">softwear-</span></div>

<!-- sample apps -->
<section class="apps-band abs" role="img" aria-label="Photo of a woman in sunglasses lying on rocks using her phone"></section>
<div class="apps-box abs">Sample<b>Apps</b></div>
<div class="store abs" style="left:468px" role="img" aria-label="Download badge"></div>
<div class="store abs" style="left:610px" role="img" aria-label="Download badge"></div>

<!-- blog -->
<h2 class="heading abs" style="left:132px;top:1896px">Latest <b>Update</b></h2>
<div class="side-label abs" style="top:1830px"><span class="rule" style="height:110px"></span><span class="word">blog-</span></div>

<article class="post abs" style="left:132px;top:1980px">
  <div class="post-photo abs" style="left:8px;top:4px;background:linear-gradient(150deg,#d8d6d2,#9a9891 50%,#3c3f3c)" role="img" aria-label="Photo of a hand in a knit sleeve holding a phone"></div>
  <div class="post-meta abs" style="left:200px;top:18px"><span>▣ 13 July</span><span>● admin</span></div>
  <h4 class="post-title abs" style="left:198px;top:52px">Lorem ipsum dolor sit amet...</h4>
  <p class="post-text abs" style="left:198px;top:74px">Lorem ipsum dolor sit aconsectetuer adip iscing elit, sediam nonummy nibh euismod tincidunt ut laoreet dolore magna aliquam erat volutpat. Ut wisi enim ad min nostrud .</p>
  <div class="read-more abs" style="left:198px;top:178px">Read More
    <svg width="14" height="14" viewBox="0 0 14 14"><circle cx="7" cy="7" r="6" stroke="#333" fill="none"/><path d="M4 7h6M8 5l2 2-2 2" stroke="#333" fill="none"/></svg></div>
</article>
<article class="post abs" style="left:578px;top:1980px">
  <div class="post-photo abs" style="left:8px;top:4px;background:linear-gradient(150deg,#e8e4dc,#b58a6a 50%,#4a3a30)" role="img" aria-label="Photo of two women looking at a phone together"></div>
  <div class="post-meta abs" style="left:200px;top:18px"><span>▣ 13 July</span><span>● admin</span></div>
  <h4 class="post-title abs" style="left:198px;top:52px">Lorem ipsum dolor sit amet...</h4>
  <p class="post-text abs" style="left:198px;top:74px">Lorem ipsum dolor sit aconsectetuer adip iscing elit, sediam nonummy nibh euismod tincidunt ut laoreet dolore magna aliquam erat volutpat. Ut wisi enim ad min nostrud .</p>
  <div class="read-more abs" style="left:198px;top:178px">Read More
    <svg width="14" height="14" viewBox="0 0 14 14"><circle cx="7" cy="7" r="6" stroke="#333" fill="none"/><path d="M4 7h6M8 5l2 2-2 2" stroke="#333" fill="none"/></svg></div>
</article>
<div class="btn abs" style="left:532px;top:2242px;width:134px;height:32px">View All Blog</div>

<!-- partners -->
<div class="partner-band abs"></div>
<svg class="abs" style="left:92px;top:2376px" width="28" height="28" viewBox="0 0 28 28"><circle cx="14" cy="14" r="12" stroke="#bbb" stroke-width="2" fill="none"/><path d="M19 14H9M13 10l-4 4 4 4" stroke="#bbb" stroke-width="2" fill="none"/></svg>
<svg class="abs" style="left:1082px;top:2376px" width="28" height="28" viewBox="0 0 28 28"><circle cx="14" cy="14" r="12" stroke="#bbb" stroke-width="2" fill="none"/><path d="M9 14h10M15 10l4 4-4 4" stroke="#bbb" stroke-width="2" fill="none"/></svg>
<div class="partner abs" style="left:132px;width:188px"><span class="dot"></span>Lumora</div>
<div class="partner abs" style="left:330px;width:186px">Brantex</div>
<div class="partner abs" style="left:526px;width:186px;font-size:14px"><span class="dot"></span>Corvane Music</div>
<div class="partner abs" style="left:722px;width:148px"><span class="dot" style="width:40px;height:40px"></span></div>
<div class="partner abs" style="left:880px;width:186px"><span class="dot"></span>Streamvale</div>

<!-- contact -->
<section class="contact-band abs" role="img" aria-label="Blurred photo of a smiling man in an office"></section>
<h2 class="contact-title abs">Keep In Touch <b>With Us</b></h2>
<p class="contact-sub abs">hendrerit in vulputate velit esse molestie consequat, vel illum dolore eu feugiat nulla facilisis at vero eros et accumsan et iusto od delenit dolore te feugait nulla.</p>
<div class="info-panel abs">
  <h3>VELMORA MEDIA</h3>
  <p>Lorem ipsum dolor sit aconsectetuer adip iscing elit, sediam nonummy nibh euismo 123. 456 &nbsp;nonummy</p>
  <div class="info-row">
    <svg width="12" height="12" viewBox="0 0 12 12"><path d="M2 1l3 0 1 3-2 1c1 2 2 3 4 4l1-2 3 1v3c-6 0-10-4-10-10z" fill="#f78f20"/></svg>
    <div>+123-456-7890<br>+123-456-7890<br>+123-456-7890</div>
  </div>
  <div class="info-row">
    <svg width="12" height="10" viewBox="0 0 12 10"><rect width="12" height="10" fill="#f78f20"/><path d="M0 0l6 5 6-5" stroke="#fff" fill="none"/></svg>
    <div><b>For Querry</b> - info@velmoramedia.tv<br><b>For Support</b> - support@velmoramedia.tv</div>
  </div>
</div>
<div class="form-panel abs"></div>
<div class="field abs" style="top:2686px;height:34px">Name</div>
<div class="field abs" style="top:2730px;height:34px">Email</div>
<div class="field abs" style="top:2774px;height:96px">Message</div>
<div class="btn submit abs">Submit</div>

<!-- footer -->
<footer class="site-footer abs">
  <div class="abs" style="left:130px;top:19px">Copyright © 2016 <span style="color:var(--orange)">VELMORA MEDIA</span> | &nbsp;All Rights Reserved.</div>
  <div class="abs" style="left:884px;top:19px">Follow Us :</div>
  <span class="social abs" style="left:966px;top:12px;background:#3b5a9a"></span>
  <span class="social abs" style="left:1002px;top:12px;background:#2fa3d8"></span>
  <span class="social abs" style="left:1038px;top:12px;background:#1a7bb5"></span>
</footer>

</body>
</html>
```